New Business Card (to reflect updated website content and graphics)

I changed some text and graphics on my website, so I need a new business card.

Target Market(s)

Mostly women, ages 30 - 60.

Industry/Entity Type

Life Coaching

Contact Information for Business Card

Included in attached Word document

Font styles to use
Sans Serif

Requirements
Must have
• I am not a creative person, so I will defer to designer. Take a look at my website, and you can get a feel for me, my style, and my target audience. Thank You!

My 3 branding colors are included in attached Word document.

```html
<!DOCTYPE html>
<html lang="en">
<head>
<meta charset="utf-8">
<title>Harbor Light Coaching – Business Card</title>
<link rel="stylesheet" href="https://fonts.googleapis.com/css2?family=Poppins:wght@400;600&display=swap">
<style>
  :root {
    --teal: #2a97b3;
    --coral: #f07e6e;
    --aqua: #5fc9c4;
    --white: #ffffff;
    --backdrop: #e4e6e8;
    --card-w: 700px;
    --card-h: 400px;
  }
  * { box-sizing: border-box; margin: 0; padding: 0; }
  html, body {
    width: 1200px; height: 900px; overflow: hidden;
    background: var(--backdrop);
    font-family: "Poppins", sans-serif;
  }
  .sheet {
    width: 1200px; height: 900px;
    display: flex; flex-direction: column; align-items: center; justify-content: center;
    gap: 40px;
  }
  .card {
    position: relative;
    width: var(--card-w); height: var(--card-h);
    border-radius: 18px;
    overflow: hidden;
    box-shadow: 0 6px 18px rgba(0,0,0,0.12);
  }

  /* Front */
  .card--front {
    background: var(--teal);
    display: flex; flex-direction: column; align-items: center; justify-content: center;
    color: var(--white);
  }
  .brand-name {
    font-weight: 400;
    font-size: 58px;
    letter-spacing: 2px;
    line-height: 1.1;
  }
  .brand-tagline {
    font-weight: 400;
    font-size: 34px;
    letter-spacing: 22px;
    margin-top: 10px;
    padding-left: 22px;
  }

  /* Back */
  .card--back { background: var(--white); }
  .wave { position: absolute; inset: 0; width: 100%; height: 100%; }
  .word-heart {
    position: absolute; left: 475px; top: 18px;
    width: 175px; height: 128px;
    border-radius: 60px 60px 80px 80px;
    background: linear-gradient(135deg, var(--teal) 0%, #7fb9c9 50%, var(--coral) 100%);
    opacity: 0.85;
  }
  .identity {
    position: absolute; left: 44px; top: 70px;
  }
  .person-name {
    color: var(--coral);
    font-weight: 600;
    font-size: 30px;
    letter-spacing: 1px;
    margin-bottom: 4px;
  }
  .credential {
    color: var(--teal);
    font-size: 17px;
    line-height: 1.45;
    letter-spacing: 0.5px;
  }
  .contacts {
    position: absolute; left: 70px; top: 218px;
    list-style: none;
  }
  .contact {
    display: flex; align-items: center; gap: 10px;
    color: var(--teal);
    font-size: 17px;
    letter-spacing: 0.4px;
    line-height: 1.75;
  }
  .contact svg { width: 18px; height: 18px; flex: none; }
</style>
</head>
<body>
<main class="sheet">

  <section class="card card--front" aria-label="Card front">
    <div class="brand-name">Harbor Light</div>
    <div class="brand-tagline">COACHING</div>
  </section>

  <section class="card card--back" aria-label="Card back">
    <svg class="wave" viewBox="0 0 700 400" preserveAspectRatio="none" aria-hidden="true">
      <path d="M0,378 C200,398 380,360 500,270 C585,222 640,182 700,172 L700,400 L0,400 Z" fill="var(--teal)"/>
      <path d="M0,354 C200,376 380,338 500,248 C570,200 630,160 700,150" fill="none" stroke="var(--coral)" stroke-width="8"/>
      <path d="M512,241 C580,192 630,146 700,136" fill="none" stroke="var(--aqua)" stroke-width="6" stroke-linecap="round"/>
    </svg>

    <div class="word-heart" role="img" aria-label="Heart shaped word cloud of coaching themes such as hope, joy, love, peace and clarity"></div>

    <div class="identity">
      <h1 class="person-name">Dana Merrow</h1>
      <p class="credential">Certified Professional Life Coach</p>
      <p class="credential">Health &amp; Wellness Coach</p>
      <p class="credential">Advanced Grief Support Specialist</p>
    </div>

    <ul class="contacts">
      <li class="contact">
        <svg viewBox="0 0 24 24"><path fill="var(--coral)" d="M6.6 10.8a15 15 0 0 0 6.6 6.6l2.2-2.2c.3-.3.7-.4 1-.2 1.1.4 2.3.6 3.6.6.6 0 1 .4 1 1V20c0 .6-.4 1-1 1A17 17 0 0 1 3 4c0-.6.4-1 1-1h3.5c.6 0 1 .4 1 1 0 1.3.2 2.5.6 3.6.1.3 0 .7-.2 1z"/></svg>
        (555) 014-2290
      </li>
      <li class="contact">
        <svg viewBox="0 0 24 24"><rect x="2" y="5" width="20" height="14" rx="2" fill="var(--coral)"/><path d="M3 6l9 7 9-7" fill="none" stroke="var(--white)" stroke-width="1.6"/></svg>
        dana@harborlightcoaching.com
      </li>
      <li class="contact">
        <svg viewBox="0 0 24 24"><circle cx="12" cy="12" r="10" fill="var(--coral)"/><path d="M2 12h20M12 2c3 3 3 17 0 20M12 2c-3 3-3 17 0 20" fill="none" stroke="var(--white)" stroke-width="1.4"/></svg>
        www.harborlightcoaching.com
      </li>
    </ul>
  </section>

</main>
</body>
</html>
```